Luxury Business Card Design for High-End Window Treatments

Gilded Slatworks
Custom Plantation Shutters & Architectural Shading Systems

⸻

BACK

Daniel Trevick
Owner

Custom Interior & Exterior Window Treatments

919-555-0148
gildedslatworks.com

I have included a picture that I’m hoping we can use on the back, but I’m also wondering if you can get rid of the ladder? Should we get rid of shutters , shades and blinds underneath Gilded Slatworks?

Target Market(s)

High-end residential homeowners, custom home builders, architects, interior designers, and luxury renovation clients seeking premium plantation shutters and motorized architectural shading systems.

Industry/Entity Type

Custom Window treatments

Contact Information for Business Card

Front Gilded Slatworks Custom Plantation Shutters Motorized Architectural Shading Systems BACK Daniel Trevick Owner 919-555-0148 GildedSlatworks.com Custom Interior & Exterior Window Treatments By Appointment

Requirements
Nice to have
• Not 100% sure on nice to halves or the color but you can definitely check out my website to get a better understanding of what I’m trying to do

```html
<!DOCTYPE html>
<html lang="en">
<head>
<meta charset="utf-8">
<title>Gilded Slatworks – Business Card</title>
<link href="https://fonts.googleapis.com/css2?family=Gilda+Display&family=Montserrat:wght@400&display=swap" rel="stylesheet">
<style>
  :root {
    --stage: #2e2620;
    --card-black: #0a0a0a;
    --card-black-soft: #1c1c1c;
    --gold: #b59c57;
    --gold-text: #c9b06b;
    --gold-bright: #f3d57a;
    --cream: #ece6da;
    --white: #f2f2f2;
    --back-gold: #a38e5e;
    --back-gold-light: #b7a476;
  }
  * { box-sizing: border-box; margin: 0; padding: 0; }
  html, body {
    width: 916px; height: 1200px; overflow: hidden;
    background: var(--stage);
  }
  .canvas { position: relative; width: 916px; height: 1200px; }
  .card {
    position: absolute; left: 71px; width: 774px; height: 460px;
    border-radius: 24px; overflow: hidden;
  }
  .card--front {
    top: 108px;
    background: linear-gradient(100deg, var(--card-black) 0%, var(--card-black-soft) 40%, var(--card-black) 70%);
  }
  .card--back {
    top: 640px;
    background: linear-gradient(90deg, var(--back-gold-light) 0%, var(--back-gold) 18%, var(--back-gold) 100%);
  }
  .photo-frame { position: absolute; inset: 0; }
  .brand-name {
    font-family: "Gilda Display", serif; color: var(--cream); font-weight: 400;
  }
  .card--front .brand-name {
    position: absolute; left: 48px; top: 48px; font-size: 34px; line-height: 38px;
  }
  .tagline {
    font-family: "Gilda Display", serif; color: var(--gold-bright);
    word-spacing: 10px;
  }
  .card--front .tagline { position: absolute; left: 48px; top: 142px; font-size: 16px; }
  .contact { position: absolute; left: 38px; top: 196px; font-family: "Montserrat", sans-serif; color: var(--white); }
  .contact__name { font-family: "Gilda Display", serif; font-size: 28px; color: var(--gold-text); line-height: 34px; }
  .contact__role { font-size: 16px; line-height: 20px; }
  .contact__specialty { font-size: 16px; line-height: 21px; margin-top: 21px; }
  .contact__line { display: flex; align-items: center; gap: 8px; font-size: 16px; line-height: 20px; }
  .contact__line--phone { margin-top: 21px; }
  .contact__line--web { margin-top: 10px; }
  .contact__line svg { width: 18px; height: 18px; fill: var(--white); }
  .contact__hours { font-size: 16px; color: var(--gold-text); margin-top: 14px; }
  .card--back .brand-name {
    position: absolute; left: 0; right: 0; top: 130px; text-align: center;
    font-size: 64px; line-height: 86px; color: var(--cream);
  }
  .card--back .tagline {
    position: absolute; left: 0; right: 0; top: 320px; text-align: center; font-size: 29px;
  }
</style>
</head>
<body>
<div class="canvas">
  <section class="card card--front">
    <svg class="photo-frame" viewBox="0 0 774 460" width="774" height="460">
      <defs>
        <linearGradient id="porchPhoto" x1="0" y1="0" x2="0" y2="1">
          <stop offset="0" stop-color="#79a7dc"/>
          <stop offset="0.3" stop-color="#b5c7d8"/>
          <stop offset="0.42" stop-color="#3b4046"/>
          <stop offset="0.62" stop-color="#5d6157"/>
          <stop offset="0.8" stop-color="#4a5a34"/>
          <stop offset="1" stop-color="#6f6a5c"/>
        </linearGradient>
      </defs>
      <path role="img" aria-label="Photo of a covered porch with exterior shades, white columns and garden chairs"
            d="M568 0 C380 70 300 330 526 460 L774 460 L774 0 Z" fill="url(#porchPhoto)"/>
      <path d="M568 0 C380 70 300 330 526 460" fill="none" stroke="var(--gold)" stroke-width="10"/>
    </svg>
    <div class="brand-name">Gilded<br>Slatworks</div>
    <div class="tagline">Shutters Shades Blinds</div>
    <div class="contact">
      <div class="contact__name">Daniel Trevick</div>
      <div class="contact__role">Owner</div>
      <div class="contact__specialty">Custom Interior &amp; Exterior<br>Window Treatments</div>
      <div class="contact__line contact__line--phone">
        <svg viewBox="0 0 24 24" aria-hidden="true"><path d="M3 9c0-3 4-5 9-5s9 2 9 5v2h-5V9c-1-.6-2.5-1-4-1s-3 .4-4 1v2H3z M6 13h12l2 7H4z"/></svg>
        919-555-0148
      </div>
      <div class="contact__line contact__line--web">
        <svg viewBox="0 0 24 24" aria-hidden="true"><circle cx="12" cy="12" r="9"/><path d="M8 7c2 1 3 0 4 2s-2 3-1 5 3 1 3 4" stroke="#111" stroke-width="1.6" fill="none"/></svg>
        GildedSlatworks.com
      </div>
      <div class="contact__hours">By Appointment</div>
    </div>
  </section>

  <section class="card card--back">
    <div class="brand-name">Gilded<br>Slatworks</div>
    <div class="tagline">Shutters Shades Blinds</div>
  </section>
</div>
</body>
</html>
```